letterhead design using our existing logo

We are a small boutique property management business based in Sydney's Northern Beaches.
We are after a sleek, simple modern letterhead (A4) incorporating our logo and its colours.
Also matching envelope (DL)
I have attached the logo with black text and white text for design options.

Target Market(s)

29-69yo Male and Female

Industry/Entity Type

Property Management

Requirements
Must have
• - Harbourline Estates logo
• - Address, number and website:
• Suite 7, 12-14 Wattlegrove Parade, Manly NSW 2095
• Tel: Carl Dorsey 0491 570 163 Marisol Quade 0491 570 218 www.harbourlinestatesgroup.com.au
Nice to have
• sleek design that looks modern and professional
Should not have
• too many colours or too busy

```html
<!DOCTYPE html>
<html lang="en">
<head>
<meta charset="utf-8">
<title>Harbourline Estates — Stationery</title>
<link rel="stylesheet" href="https://fonts.googleapis.com/css2?family=Arimo:wght@400;700&display=swap">
<style>
  :root {
    --teal: #137b8c;
    --ink: #1b1b1b;
    --paper: #ffffff;
    --backdrop: #e8e5e1;
    --shadow: rgba(0, 0, 0, 0.18);
  }
  * { margin: 0; padding: 0; box-sizing: border-box; }
  html, body {
    width: 1200px; height: 1000px; overflow: hidden;
    background: var(--backdrop);
    font-family: "Arimo", Arial, sans-serif;
    color: var(--ink);
  }
  .canvas { position: relative; width: 1200px; height: 1000px; }

  .sheet {
    position: absolute;
    background: var(--paper);
    box-shadow: 0 3px 10px var(--shadow);
    overflow: hidden;
  }
  .side-band {
    position: absolute; top: 0; left: 0; bottom: 0;
    background: var(--teal);
    display: flex; align-items: center; justify-content: center;
  }
  .side-band__text {
    writing-mode: vertical-rl;
    transform: rotate(180deg);
    color: #fff;
    font-size: 10px;
    letter-spacing: 0.2px;
    white-space: nowrap;
  }

  .brand {
    position: absolute;
    display: flex; align-items: center; gap: 8px;
  }
  .brand__dot {
    width: 12px; height: 12px; border-radius: 50%;
    background: var(--teal);
  }
  .brand__name {
    font-weight: 700; font-size: 23px;
    color: var(--ink);
    text-transform: uppercase;
    letter-spacing: -0.3px;
  }

  .contact {
    position: absolute;
    text-align: right;
    font-size: 10.5px;
    line-height: 13px;
  }
  .contact__address { margin-bottom: 13px; }

  /* A4 letterhead */
  .letterhead { left: 46px; top: 80px; width: 595px; height: 840px; }
  .letterhead .side-band { width: 20px; }
  .letterhead .brand { left: 42px; top: 56px; }
  .letterhead .contact { right: 30px; top: 40px; }

  /* DL envelope front */
  .envelope-front { left: 538px; top: 200px; width: 623px; height: 311px; }
  .envelope-front .side-band { width: 21px; }
  .envelope-front .brand { left: 41px; top: 56px; }
  .envelope-front .contact { right: 29px; top: 40px; }

  /* DL envelope back */
  .envelope-back { left: 538px; top: 531px; width: 623px; height: 309px; }
  .envelope-back__flap {
    position: absolute; left: 0; top: 0; right: 0; height: 106px;
    background: var(--teal);
    border-bottom-left-radius: 48px;
    display: flex; align-items: center; justify-content: center;
  }
  .envelope-back__web {
    color: #fff; font-size: 11px; letter-spacing: 2px;
    transform: translateY(-2px);
  }
  .envelope-back__fold {
    position: absolute; left: 0; right: 0; top: 106px; height: 8px;
    background: linear-gradient(#eeeeee, #ffffff);
  }
</style>
</head>
<body>
<main class="canvas">

  <section class="sheet letterhead" aria-label="A4 letterhead">
    <div class="side-band">
      <span class="side-band__text">info@harbourlinestatesgroup.com.au | www.harbourlinestatesgroup.com.au</span>
    </div>
    <div class="brand">
      <span class="brand__name">Harbourline Estates</span>
      <span class="brand__dot"></span>
    </div>
    <address class="contact" style="font-style:normal">
      <p class="contact__address">Suite 7, 12-14 Wattlegrove Parade<br>Manly NSW 2095</p>
      <p>Carl Dorsey 0491 570 163<br>Marisol Quade 0491 570 218</p>
    </address>
  </section>

  <section class="sheet envelope-front" aria-label="DL envelope, front">
    <div class="side-band">
      <span class="side-band__text">www.harbourlinestatesgroup.com.au</span>
    </div>
    <div class="brand">
      <span class="brand__name">Harbourline Estates</span>
      <span class="brand__dot"></span>
    </div>
    <address class="contact" style="font-style:normal">
      <p class="contact__address">Suite 7, 12-14 Wattlegrove Parade<br>Manly NSW 2095</p>
      <p>Carl Dorsey 0491 570 163<br>Marisol Quade 0491 570 218</p>
    </address>
  </section>

  <section class="sheet envelope-back" aria-label="DL envelope, back">
    <div class="envelope-back__flap">
      <span class="envelope-back__web">www.harbourlinestatesgroup.com.au</span>
    </div>
    <div class="envelope-back__fold"></div>
  </section>

</main>
</body>
</html>
```